Vindgerdi - Start-up company selling electricity

Hello let me tell you about Vindgerdi.

Vindgerdi is start-up company selling electricity in Iceland. The operations of the company consist of making power usage forecasts for our customers, purchasing the electricity wholesale from the energy producers, and selling the electricity to the consumer. We are focused on tech by using optimization and machine learning to minimize electricity prices to our customers. Our marketing strategy is to portray a tech company mindset and to show dedication to driving down the electricity price on the market.

We need your help to make our website pop. Possible concepts to work with are as follows:

- Iceland the land of ice and fire
- Green energy
- Innovation
- Tech and data science

Link to our website: https://prufa.vindgerdi-example.is/
We are open to ideas.
Thank you!

Target Market(s)

Electricity consumers both homes and companies.

Number of Pages Required

1 page

Font styles to use
Serif
Sans Serif

```html
<!DOCTYPE html>
<html lang="en">
<head>
<meta charset="utf-8">
<title>Vindgerdi – Selling and Generating Energy in Iceland</title>
<link href="https://fonts.googleapis.com/css2?family=Montserrat:wght@400;500;600;700;800&family=Playfair+Display:wght@600;700&display=swap" rel="stylesheet">
<style>
  :root{
    --red:#a8271f;
    --red-dark:#8c1f18;
    --navy:#1c2b4b;
    --white:#ffffff;
    --ink:#2b2b2b;
    --muted:#6d6d6d;
    --paper:#f3f3f3;
    --footer:#e6e7e9;
  }
  *{box-sizing:border-box;margin:0;padding:0}
  html,body{width:673px;height:1200px;overflow:hidden}
  body{font-family:"Montserrat",Arial,sans-serif;color:var(--ink);background:var(--white);position:relative}

  .topbar{height:14px;background:var(--red);color:var(--white);font-size:6px;display:flex;align-items:center;justify-content:space-between;padding:0 30px}
  .topbar .contacts{display:flex;gap:18px}

  .header{height:40px;display:flex;align-items:center;justify-content:space-between;padding:0 30px;background:var(--white)}
  .brand{display:flex;align-items:center;gap:6px;font-weight:800;font-size:15px;color:var(--red);letter-spacing:.5px}
  .brand-dot{width:11px;height:11px;border-radius:50%;background:var(--navy)}
  .nav{display:flex;gap:18px;font-size:6.5px;font-weight:500;color:var(--ink)}

  .hero{position:relative;height:323px;background:linear-gradient(110deg,#1d1e26 0%,#2e2c33 45%,#6a5844 62%,#2a2830 80%,#17171d 100%);color:var(--white)}
  .hero-glow{position:absolute;left:360px;top:60px;width:200px;height:200px;border-radius:50%;background:radial-gradient(circle,rgba(255,225,170,.55),rgba(255,190,120,.15) 45%,transparent 70%)}
  .hero-copy{position:absolute;left:34px;top:80px;width:300px}
  .hero h1{font-size:26px;line-height:1.15;font-weight:800}
  .hero p{font-size:7.5px;margin-top:9px;opacity:.9}
  .hero-actions{display:flex;gap:10px;margin-top:14px}
  .btn{display:inline-flex;align-items:center;justify-content:center;height:20px;padding:0 12px;font-size:7px;font-weight:700;text-transform:uppercase;border-radius:2px;color:var(--white)}
  .btn-red{background:var(--red)}
  .btn-navy{background:var(--navy);border:1px solid rgba(255,255,255,.5)}
  .slider-dots{position:absolute;right:22px;top:148px;display:flex;flex-direction:column;gap:5px}
  .slider-dots span{width:5px;height:5px;border-radius:50%;background:rgba(255,255,255,.5)}
  .slider-dots span:first-child{background:var(--white)}

  .offer{position:relative;z-index:2;height:320px;background:linear-gradient(180deg,#ffffff 0%,#f1f2f4 55%,#e9eaed 100%);border-radius:0 0 90px 90px;text-align:center}
  .offer h2{font-family:"Playfair Display",Georgia,serif;font-size:21px;padding-top:30px;color:var(--red);font-weight:600}
  .offer h2 strong{color:var(--navy);font-weight:700}
  .cards{position:relative;height:200px;margin-top:10px}
  .card{position:absolute;background:var(--white);box-shadow:0 4px 12px rgba(0,0,0,.12);padding:32px 12px 12px;font-size:6px;line-height:1.5;color:var(--muted)}
  .card h3{font-size:8px;color:var(--navy);font-weight:700;margin-bottom:6px}
  .card-left{left:90px;top:42px;width:140px;height:136px}
  .card-right{left:437px;top:42px;width:146px;height:136px}
  .card-price{left:258px;top:18px;width:158px;height:172px;background:var(--navy);color:#cfd6e6;padding-top:14px}
  .card-price h3{color:var(--white)}
  .icon{position:absolute;left:50%;top:-16px;width:32px;height:32px;margin-left:-16px;border-radius:50%;background:var(--red);border:3px solid var(--white);display:flex;align-items:center;justify-content:center}
  .price{font-size:16px;font-weight:700;color:#e3483d;margin-top:10px;line-height:1}
  .unit{font-size:5.5px;color:#cfd6e6}
  .card-actions{display:flex;justify-content:center;gap:5px;margin-top:8px}
  .btn-sm{height:14px;padding:0 7px;font-size:5.5px;border-radius:2px;display:inline-flex;align-items:center;font-weight:700;text-transform:uppercase}
  .btn-outline-red{border:1px solid var(--red);color:var(--red)}
  .btn-fill-navy{background:var(--navy);color:var(--white)}

  .choose{position:relative;z-index:1;margin-top:-90px;height:330px;background:var(--red);color:var(--white);text-align:center;border-radius:0 0 90px 90px;padding-top:118px}
  .drop{width:24px;height:24px;margin:0 auto 8px;border-radius:50%;background:var(--white);display:flex;align-items:center;justify-content:center}
  .choose h2{font-family:"Playfair Display",Georgia,serif;font-size:17px;font-weight:600}
  .choose p{font-size:6.5px;margin-top:5px;opacity:.9}
  .btn-ghost{margin-top:10px;height:16px;padding:0 12px;border:1px solid var(--white);font-size:6px;display:inline-flex;align-items:center;font-weight:700;text-transform:uppercase;color:var(--white)}

  .footer{position:absolute;left:0;top:900px;width:673px;height:278px;background:linear-gradient(180deg,#eceef1,#dfe2e6);padding:50px 40px 0}
  .footer-cols{display:flex;gap:40px;align-items:flex-start}
  .col h4{font-size:8px;font-weight:700;color:var(--navy);margin-bottom:8px}
  .col ul{list-style:none;font-size:6px;color:var(--muted);line-height:2}
  .col li{display:flex;align-items:center;gap:5px}
  .bullet{width:4px;height:4px;border-radius:50%;background:var(--red)}
  .col-sitemap{width:120px}
  .col-contact{width:130px}
  .col-info{width:110px}
  .call{width:92px;height:92px;border-radius:50%;background:var(--navy);color:var(--white);display:flex;flex-direction:column;align-items:center;justify-content:center;font-size:7px;font-weight:700;gap:3px;margin-left:10px;margin-top:-6px;box-shadow:0 0 0 6px rgba(28,43,75,.15)}
  .call small{font-size:6px;font-weight:500}

  .copyright{position:absolute;left:0;bottom:0;width:673px;height:22px;background:var(--navy);color:#c9cfdc;font-size:5.5px;display:flex;align-items:center;justify-content:center}
</style>
</head>
<body>
  <div class="topbar">
    <span>English ▾</span>
    <div class="contacts"><span>☎ 555-0140</span><span>✉ info@vindgerdi-example.is</span></div>
  </div>

  <header class="header">
    <div class="brand"><span class="brand-dot"></span>VINDGERDI</div>
    <nav class="nav">
      <span>Terms of Business</span><span>Questions &amp; Answers</span><span>About Vindgerdi</span><span>Contact Us</span>
    </nav>
  </header>

  <section class="hero">
    <div class="hero-glow" role="img" aria-label="Photo of hands holding a tablet with a glowing light bulb above it"></div>
    <div class="hero-copy">
      <h1>Vindgerdi Selling and Generating Energy In Iceland</h1>
      <p>Everything you need to know about how we can help you with electricity</p>
      <div class="hero-actions">
        <span class="btn btn-red">Register Now</span>
        <span class="btn btn-navy">Get a Quote</span>
      </div>
    </div>
    <div class="slider-dots"><span></span><span></span><span></span></div>
  </section>

  <section class="offer" role="img" aria-label="Faint photo of wind turbines behind the offer cards">
    <h2>Same Electricity <strong>– Just Cheaper!</strong></h2>
    <div class="cards">
      <article class="card card-left">
        <div class="icon"><svg width="14" height="14" viewBox="0 0 14 14"><path d="M8 1 3 8h4l-1 5 5-7H7z" fill="#fff"/></svg></div>
        <h3>Welcome To Business</h3>
        <p>It can be said that by trading with Vindgerdi, you support the development of the Icelandic electricity market.</p>
        <div class="card-actions"><span class="btn-sm btn-outline-red">Register</span><span class="btn-sm btn-fill-navy">Company</span></div>
      </article>
      <article class="card card-price">
        <h3>Price List</h3>
        <div class="price">9.95</div><div class="unit">kr/kWh</div>
        <div class="price">5.22</div><div class="unit">kr/kWh</div>
        <p style="margin-top:8px">electric production<br>Make a price comparison</p>
      </article>
      <article class="card card-right">
        <div class="icon"><svg width="14" height="14" viewBox="0 0 14 14"><circle cx="7" cy="7" r="3" fill="none" stroke="#fff" stroke-width="1.6"/><path d="M7 1v2M7 11v2M1 7h2M11 7h2M2.8 2.8l1.4 1.4M9.8 9.8l1.4 1.4M2.8 11.2l1.4-1.4M9.8 4.2l1.4-1.4" stroke="#fff" stroke-width="1.4"/></svg></div>
        <h3>The Future Is Exciting</h3>
        <p>Let's make the electricity system smarter together. Vindgerdi uses artificial intelligence, data science and automation to minimize costs and promote sustainability.</p>
      </article>
    </div>
  </section>

  <section class="choose">
    <div class="drop"><svg width="10" height="12" viewBox="0 0 10 12"><path d="M5 0C5 0 0 6 0 8a5 4 0 0 0 10 0C10 6 5 0 5 0z" fill="#a8271f"/></svg></div>
    <h2>You Choose Where You Buy Electricity</h2>
    <p>Did you know that you can decide where to buy electricity for your home, regardless of location?</p>
    <span class="btn-ghost">Subscribe</span>
  </section>

  <footer class="footer">
    <div class="footer-cols">
      <div class="col col-sitemap">
        <h4>Sitemap</h4>
        <ul><li><span class="bullet"></span>Terms of Business</li><li><span class="bullet"></span>Questions &amp; Answers</li><li><span class="bullet"></span>About Vindgerdi</li></ul>
      </div>
      <div class="col col-contact">
        <h4>Contact Us</h4>
        <ul><li><span class="bullet"></span>Sólvangur 12, 110 Reykjavík</li><li><span class="bullet"></span>info@vindgerdi-example.is</li><li><span class="bullet"></span>555-0140</li></ul>
      </div>
      <div class="col col-info">
        <h4>Useful Info</h4>
        <ul><li><span class="bullet"></span>Kt: 000000-0000</li><li><span class="bullet"></span>Reikn: 0000-00-000000</li><li><span class="bullet"></span>VSK: 000000</li></ul>
      </div>
      <div class="call">
        <svg width="14" height="14" viewBox="0 0 14 14"><path d="M3 1h2.5l1 3-1.6 1a7 7 0 0 0 4.1 4.1l1-1.6 3 1V11a2 2 0 0 1-2 2A11 11 0 0 1 1 3a2 2 0 0 1 2-2z" fill="#fff"/></svg>
        <span>555-0140</span><small>Call Now</small>
      </div>
    </div>
  </footer>

  <div class="copyright">© 2024 Vindgerdi. All rights reserved.</div>
</body>
</html>
```